Business Card Design for Occupational Medicine Start Up Company

We need to design a professional business card. We are a healthcare company providing occupational medicine services to blue collar industries. We are professional, efficient and high quality service providers.

Target Market(s)

Blue Collar Industry: Shipbuilding, Ports, Trucking Companies; The Executives and Safety Officers for these companies

Industry/Entity Type

Healthcare

Contact Information for Business Card

Logo, Name, Title, Email, Phone

Other font styles liked:
• Please match our Brand Guide

Requirements
Must have
• Our Company Colors and Logo

```html
<!DOCTYPE html>
<html lang="en">
<head>
<meta charset="utf-8">
<title>CrewPoint Health — Business Card</title>
<link rel="stylesheet" href="https://fonts.googleapis.com/css2?family=Montserrat:wght@400;500;700;800&display=swap">
<style>
  :root {
    --navy: #2a2f7e;
    --royal: #2f4fa6;
    --sky: #3a9ad8;
    --orange: #f2b134;
    --ink: #2a2a3a;
    --white: #ffffff;
    --backdrop: #e6e8ec;
  }
  * { box-sizing: border-box; margin: 0; padding: 0; }
  html, body {
    width: 1200px; height: 1186px; overflow: hidden;
    background: var(--backdrop);
    font-family: "Montserrat", sans-serif;
  }
  .sheet {
    width: 1200px; height: 1186px;
    display: flex; flex-direction: column; align-items: center; justify-content: center;
    gap: 60px;
  }
  .card {
    position: relative;
    width: 840px; height: 480px;
    border-radius: 28px;
    overflow: hidden;
    box-shadow: 0 14px 36px rgba(20, 30, 60, 0.22);
  }
  /* Front */
  .card--front {
    background: linear-gradient(30deg, var(--navy) 0%, var(--royal) 45%, var(--sky) 100%);
    display: flex; align-items: center; justify-content: center;
  }
  .brand {
    display: flex; align-items: center; gap: 22px;
    font-weight: 800; letter-spacing: 0.02em;
  }
  .brand__dot { border-radius: 50%; flex: none; }
  .card--front .brand { color: var(--white); font-size: 54px; }
  .card--front .brand__dot { width: 40px; height: 40px; background: var(--white); }

  /* Back */
  .card--back { background: var(--white); color: var(--ink); }
  .card--back .brand {
    position: absolute; left: 60px; top: 70px;
    color: var(--navy); font-size: 38px;
  }
  .card--back .brand__dot { width: 30px; height: 30px; background: var(--sky); }
  .divider { position: absolute; left: 60px; right: 0; top: 318px; height: 3px; }
  .person { position: absolute; left: 60px; top: 246px; }
  .person__name { font-weight: 800; font-size: 30px; color: var(--navy); }
  .person__title { font-weight: 400; font-size: 18px; color: var(--ink); margin-top: 2px; }
  .address {
    position: absolute; right: 50px; top: 252px;
    text-align: right; font-size: 18px; line-height: 1.45; color: var(--ink);
  }
  .contacts {
    position: absolute; left: 60px; top: 340px;
    list-style: none; font-size: 19px; line-height: 1.75; color: var(--ink);
  }
  .contacts li { display: flex; align-items: center; gap: 14px; }
  .contacts svg { width: 18px; height: 18px; flex: none; }
</style>
</head>
<body>
<main class="sheet">
  <section class="card card--front" aria-label="Card front">
    <div class="brand"><span class="brand__dot"></span>CREWPOINT HEALTH</div>
  </section>

  <section class="card card--back" aria-label="Card back">
    <div class="brand"><span class="brand__dot"></span>CREWPOINT HEALTH</div>

    <div class="person">
      <p class="person__name">Daniel Reyes</p>
      <p class="person__title">CEO &amp; Founder</p>
    </div>

    <address class="address" style="font-style:normal">
      418 Harbor Ave, #112<br>Lakemont, OH 43000
    </address>

    <svg class="divider" viewBox="0 0 780 3" preserveAspectRatio="none" aria-hidden="true">
      <rect x="0" y="0" width="260" height="3" fill="var(--sky)"/>
      <rect x="260" y="0" width="240" height="3" fill="var(--navy)"/>
      <rect x="500" y="0" width="280" height="3" fill="var(--orange)"/>
    </svg>

    <ul class="contacts">
      <li>
        <svg viewBox="0 0 24 24" aria-hidden="true"><path fill="var(--sky)" d="M6.6 10.8a15.2 15.2 0 0 0 6.6 6.6l2.2-2.2a1 1 0 0 1 1-.25 11.4 11.4 0 0 0 3.6.57 1 1 0 0 1 1 1V20a1 1 0 0 1-1 1A17 17 0 0 1 3 4a1 1 0 0 1 1-1h3.5a1 1 0 0 1 1 1c0 1.25.2 2.45.57 3.6a1 1 0 0 1-.25 1z"/></svg>
        800-555-0142
      </li>
      <li>
        <svg viewBox="0 0 24 24" aria-hidden="true"><rect x="2" y="5" width="20" height="14" rx="2" fill="var(--sky)"/><path d="M3 6l9 7 9-7" stroke="#fff" stroke-width="1.6" fill="none"/></svg>
        hello@crewpointhealth.com
      </li>
      <li>
        <svg viewBox="0 0 24 24" aria-hidden="true"><circle cx="12" cy="12" r="10" fill="var(--sky)"/><path d="M2 12h20M12 2c3 3 3 17 0 20M12 2c-3 3-3 17 0 20" stroke="#fff" stroke-width="1.4" fill="none"/></svg>
        www.crewpointhealth.com
      </li>
    </ul>
  </section>
</main>
</body>
</html>
```